Haulage company, lets use ruby red white and some 3rd color for web design. and Garvel Pryce Transport logo

Target Market(s)

Transport industry

Industry/Entity Type

transport

Number of Pages Required

2 page

Requirements
Must have
• Logo

```html
<!DOCTYPE html>
<html lang="en">
<head>
<meta charset="utf-8">
<title>Garvel Pryce Transport</title>
<link href="https://fonts.googleapis.com/css2?family=Lato:wght@400;700;900&display=swap" rel="stylesheet">
<style>
:root{
  --ruby:#5c0822;
  --ruby-dark:#4a0619;
  --teal:#45cfcd;
  --ink:#333;
  --muted:#666;
  --light:#f1f1f3;
  --white:#fff;
}
*{box-sizing:border-box;margin:0;padding:0}
html,body{width:1200px;height:3697px;overflow:hidden}
body{position:relative;font-family:'Lato',sans-serif;color:var(--ink);background:var(--white)}
.abs{position:absolute}
a{color:inherit;text-decoration:none}

/* header */
.brand-block{left:0;top:0;width:520px;height:118px;background:var(--ruby);clip-path:polygon(0 0,520px 0,385px 118px,0 118px)}
.brand-name{left:0;width:465px;top:62px;text-align:center;color:var(--white);font-weight:700;font-size:25px}
.contact-item{display:flex;align-items:center;gap:14px;top:14px}
.contact-ico{width:44px;height:44px;border-radius:50%;background:var(--teal);display:flex;align-items:center;justify-content:center}
.contact-label{font-size:13px;color:#222}
.contact-value{font-size:17px;color:#222}
.nav{top:84px;left:0;width:1200px;font-size:15px;color:#222}
.nav a{position:absolute}
.nav a.active{color:var(--ruby);font-weight:700}

/* hero */
.hero-strip{left:0;top:118px;width:40px;height:568px;background:var(--ruby)}
.hero-photo{left:40px;top:118px;width:1160px;height:568px;background:linear-gradient(100deg,#12161c 0%,#2a3240 35%,#6b7c93 60%,#9aa8b8 80%,#4b5a4a 100%)}
.hero-title{left:113px;top:218px;color:var(--white);font-weight:700;font-size:74px;line-height:86px}
.hero-text{left:112px;top:418px;width:540px;color:var(--white);font-size:19.5px;line-height:25px}
.btn{background:var(--teal);color:var(--white);font-weight:700;display:flex;align-items:center;justify-content:center}
.hero-btn{left:111px;top:532px;width:154px;height:37px;font-size:16px}
.hero-arrow{left:1083px;width:37px;height:37px;border-radius:50%;border:2px solid var(--white);display:flex;align-items:center;justify-content:center}

/* headings */
.section-title{left:0;width:1200px;text-align:center;color:var(--ruby);font-weight:700;font-size:40px}

/* services */
.service-card{width:470px;height:505px;top:852px;background:var(--white);border-radius:18px 18px 0 0;box-shadow:0 0 8px rgba(0,0,0,.12)}
.service-photo{position:absolute;left:0;top:0;width:470px;height:230px;border-radius:18px 18px 0 0}
.service-ico{position:absolute;left:345px;top:180px;width:88px;height:88px;border-radius:50%;background:var(--ruby);border:6px solid var(--white);display:flex;align-items:center;justify-content:center}
.service-title{position:absolute;left:27px;top:288px;color:var(--ruby);font-weight:700;font-size:30px}
.service-text{position:absolute;left:27px;top:338px;width:420px;font-size:13.6px;line-height:21px;color:var(--muted)}
.read-more{color:var(--teal);font-weight:700;font-size:15px}

/* how it works */
.how-band{left:0;top:1443px;width:1200px;height:519px;background:var(--light)}
.step-circle{width:124px;height:124px;border-radius:50%;background:var(--white);top:1621px;display:flex;align-items:center;justify-content:center;box-shadow:0 0 10px rgba(0,0,0,.05)}
.step-circle .inner{width:96px;height:96px;border-radius:50%;border:1.5px dashed var(--teal);display:flex;align-items:center;justify-content:center}
.step-num{width:34px;height:34px;border-radius:50%;background:var(--teal);color:var(--white);font-size:15px;display:flex;align-items:center;justify-content:center;top:1617px}
.step-title{width:254px;text-align:center;top:1764px;color:var(--ruby);font-weight:700;font-size:21px}
.step-text{width:254px;text-align:center;top:1799px;color:var(--muted);font-size:15px;line-height:22px}

/* about */
.about-back{left:111px;top:2195px;width:434px;height:223px;background:var(--ruby);clip-path:polygon(0 40px,40px 0,100% 0,100% 100%,0 100%)}
.about-photo-a{left:127px;top:2048px;width:225px;height:357px;background:linear-gradient(180deg,#8a97a6 0%,#c9cdd3 45%,#a13a4a 70%,#6f6f72 100%)}
.about-stat{left:365px;top:2048px;width:176px;height:154px;background:var(--teal);color:var(--white);padding:22px 0 0 34px}
.about-stat b{font-size:42px;font-weight:700;display:block;line-height:46px}
.about-stat span{font-size:16px;line-height:24px;display:block;margin-top:4px}
.about-bar{left:552px;top:2048px;width:6px;height:154px;background:var(--teal)}
.about-photo-b{left:365px;top:2211px;width:193px;height:194px;background:linear-gradient(180deg,#58708f 0%,#b9c4d1 40%,#e6e8ea 60%,#4a4c4d 100%)}
.about-title{left:631px;top:2035px;color:var(--ruby);font-weight:700;font-size:40px}
.about-text{left:630px;top:2113px;width:460px;font-size:16px;line-height:25px;color:var(--muted)}
.about-btn{left:630px;top:2380px;width:154px;height:37px;font-size:17px}

/* blog */
.blog-card{width:313px;top:2589px;height:390px}
.blog-photo{position:absolute;left:0;top:0;width:313px;height:203px}
.blog-panel{position:absolute;left:20px;top:139px;width:280px;height:251px;background:var(--white)}
.blog-meta{position:absolute;left:14px;top:24px;display:flex;align-items:center;gap:22px;font-size:13px;color:#888}
.blog-date{background:var(--ruby);color:var(--white);font-size:11px;padding:4px 8px}
.blog-title{position:absolute;left:14px;top:70px;width:260px;color:var(--ruby);font-weight:700;font-size:21px;line-height:25px}
.blog-text{position:absolute;left:14px;top:134px;width:260px;color:var(--muted);font-size:14.5px;line-height:23px}
.blog-more{position:absolute;left:14px;top:210px}
.dots{top:2998px;left:568px;display:flex;gap:8px;align-items:center}
.dots i{display:block;width:9px;height:9px;border-radius:50%;background:#555}
.dots i.on{width:32px;border-radius:5px;background:var(--teal)}

/* footer */
.footer{left:0;top:3095px;width:1200px;height:547px;background:var(--ruby);color:var(--white)}
.foot-brand{left:0;width:465px;top:3200px;text-align:center;font-weight:700;font-size:26px}
.foot-divider{left:383px;top:3160px;width:2px;height:62px;background:var(--teal)}
.news-title{left:420px;top:3168px;font-size:27px;font-weight:700}
.news-sub{left:420px;top:3204px;font-size:12.5px;line-height:18px;width:240px}
.news-input{left:715px;top:3174px;width:238px;height:46px;border:1px solid #d9c5cb;font-size:12.5px;padding-left:18px;display:flex;align-items:center}
.news-btn{left:966px;top:3174px;width:123px;height:46px;font-size:18px}
.foot-rule{left:111px;top:3283px;width:978px;height:1px;background:#8a4458}
.col-head{top:3350px;font-size:20px;font-weight:700}
.col-line{width:88px;height:2px;background:var(--teal);top:3386px}
.col-line::after{content:"";position:absolute;right:-2px;top:-3px;width:8px;height:8px;border-radius:50%;background:var(--teal)}
.foot-about{left:111px;top:3412px;width:240px;font-size:14.5px;line-height:22px}
.social{top:3525px;width:46px;height:40px;background:var(--teal)}
.link-list{list-style:none;font-size:15px;top:3410px}
.link-list li{height:36px;display:flex;align-items:center;gap:16px}
.recent{left:858px;width:235px;display:flex;gap:12px}
.recent-photo{width:68px;height:66px;flex:none}
.recent b{display:block;font-size:15px;line-height:22px}
.recent small{display:block;font-size:12.5px;margin-top:4px}
.bottom-bar{left:0;top:3642px;width:1200px;height:55px;background:var(--teal);color:var(--white);font-size:15px;display:flex;align-items:center;justify-content:center}
</style>
</head>
<body>

<!-- header -->
<div class="abs brand-block"></div>
<div class="abs brand-name">Garvel Pryce Transport</div>

<div class="abs contact-item" style="left:562px">
  <div class="contact-ico"><svg width="18" height="14" viewBox="0 0 18 14"><rect x="1" y="1" width="16" height="12" rx="1.5" fill="none" stroke="#fff" stroke-width="2"/><path d="M1 2 9 8 17 2" fill="none" stroke="#fff" stroke-width="2"/></svg></div>
  <div><div class="contact-label">Email</div><div class="contact-value">hello@garvelpryce.com</div></div>
</div>
<div class="abs contact-item" style="left:898px">
  <div class="contact-ico"><svg width="18" height="18" viewBox="0 0 24 24"><path d="M6.6 10.8a15 15 0 0 0 6.6 6.6l2.2-2.2c.3-.3.7-.4 1-.2 1.1.4 2.3.6 3.6.6.6 0 1 .4 1 1V20c0 .6-.4 1-1 1A17 17 0 0 1 3 4c0-.6.4-1 1-1h3.5c.6 0 1 .4 1 1 0 1.3.2 2.5.6 3.6.1.3 0 .7-.2 1z" fill="#fff"/></svg></div>
  <div><div class="contact-label">Call Us</div><div class="contact-value">+ 1 555 014 2276</div></div>
</div>

<nav class="abs nav">
  <a class="active" style="left:525px">Home</a>
  <a style="left:641px">About Us</a>
  <a style="left:778px">Services</a>
  <a style="left:909px">Blog</a>
  <a style="left:1013px">Contact Us</a>
</nav>

<!-- hero -->
<div class="abs hero-strip"></div>
<div class="abs hero-photo" role="img" aria-label="Articulated cold storage truck driving on a highway under a cloudy sky"></div>
<h1 class="abs hero-title">Welcome to Garvel<br>&nbsp;Pryce Transport</h1>
<p class="abs hero-text">Lorem ipsum dolor sit amet, consectetur adipiscing elit, sed do eiusmod tempor incididunt ut labore et dolore magna aliqua.</p>
<a class="abs btn hero-btn">Contact Us</a>
<div class="abs hero-arrow" style="top:353px"><svg width="12" height="16" viewBox="0 0 12 16"><path d="M9 2 3 8l6 6" fill="none" stroke="#fff" stroke-width="2.4"/></svg></div>
<div class="abs hero-arrow" style="top:414px;background:#fff"><svg width="12" height="16" viewBox="0 0 12 16"><path d="m3 2 6 6-6 6" fill="none" stroke="#555" stroke-width="2.4"/></svg></div>

<!-- services -->
<h2 class="abs section-title" style="top:767px">Our Services</h2>

<article class="abs service-card" style="left:111px">
  <div class="service-photo" role="img" aria-label="White semi trucks on an open road" style="background:linear-gradient(180deg,#b6c3cf 0%,#dfe3e6 50%,#7d7f80 75%,#4c4d4e 100%)"></div>
  <div class="service-ico"><svg width="46" height="34" viewBox="0 0 46 34" fill="none" stroke="#fff" stroke-width="2"><rect x="2" y="4" width="28" height="20"/><path d="M30 10h8l6 7v7H30z"/><circle cx="10" cy="27" r="4"/><circle cx="36" cy="27" r="4"/><path d="M7 8v12M12 8v12M17 8v12M22 8v12"/></svg></div>
  <h3 class="service-title">Road Transportation</h3>
  <p class="service-text">Lorem ipsum dolor sit amet, consectetur adipiscing elit, sed do eiusmod tempor incididunt ut labore et dolore magna aliqua. Ut enim ad minim veniam, quis nostrud exercitation ullamco laboris nisi ut aliquip ex ea commodo consequat.</p>
  <a class="read-more abs" style="left:27px;top:443px">Read More ...</a>
</article>

<article class="abs service-card" style="left:617px">
  <div class="service-photo" role="img" aria-label="Blue diesel locomotive pulling a freight train through green countryside" style="background:linear-gradient(180deg,#8fa0b0 0%,#5a6470 40%,#3f6aa8 55%,#4e7a3a 80%,#6a7a5a 100%)"></div>
  <div class="service-ico"><svg width="30" height="38" viewBox="0 0 30 38" fill="none" stroke="#fff" stroke-width="2"><rect x="3" y="2" width="24" height="28" rx="5"/><path d="M3 16h24M9 8h12"/><circle cx="9" cy="23" r="2"/><circle cx="21" cy="23" r="2"/><path d="M8 30 3 36M22 30l5 6"/></svg></div>
  <h3 class="service-title">Rail Transportation</h3>
  <p class="service-text">Lorem ipsum dolor sit amet, consectetur adipiscing elit, sed do eiusmod tempor incididunt ut labore et dolore magna aliqua. #Ut enim ad minim veniam, quis nostrud exercitation ullamco laboris nisi ut aliquip ex ea commodo consequat.</p>
  <a class="read-more abs" style="left:27px;top:441px">Read More ...</a>
</article>

<!-- how it works -->
<div class="abs how-band"></div>
<h2 class="abs section-title" style="top:1519px">How It Works</h2>
<svg class="abs" style="left:0;top:1600px" width="1200" height="160" viewBox="0 0 1200 160" fill="none" stroke="#45cfcd" stroke-width="1.2" stroke-dasharray="4 3">
  <path d="M268 113c40 30 110 30 150-6"/>
  <path d="M533 68c60-10 110 10 140 30"/>
  <path d="M783 118c60 10 120 5 155-20"/>
</svg>

<div class="abs step-circle" style="left:156px"><div class="inner"><svg width="44" height="44" viewBox="0 0 44 44" fill="none" stroke="#45cfcd" stroke-width="1.8"><rect x="8" y="7" width="22" height="30" rx="2"/><path d="M14 5h10v5H14zM13 17h12M13 23h8"/><circle cx="32" cy="31" r="7"/><path d="m29 31 2 2 4-4"/></svg></div></div>
<div class="abs step-num" style="left:254px">01</div>
<h4 class="abs step-title" style="left:91px">Parcel Register</h4>
<p class="abs step-text" style="left:91px">Quis ipsum suspendisse ultrices gravida. Risus commodo viverra maecenas accumsan facilisis.</p>

<div class="abs step-circle" style="left:411px"><div class="inner"><svg width="44" height="44" viewBox="0 0 44 44" fill="none" stroke="#45cfcd" stroke-width="1.8"><rect x="20" y="6" width="18" height="26"/><path d="M24 10v18M28 10v18M32 10v18"/><rect x="8" y="24" width="10" height="10"/><circle cx="12" cy="38" r="2.5"/><path d="M4 38h34"/></svg></div></div>
<div class="abs step-num" style="left:508px">02</div>
<h4 class="abs step-title" style="left:346px">Parcel Loading</h4>
<p class="abs step-text" style="left:346px">Quis ipsum suspendisse ultrices gravida. Risus commodo viverra maecenas accumsan facilisis.</p>

<div class="abs step-circle" style="left:665px"><div class="inner"><svg width="44" height="44" viewBox="0 0 44 44" fill="none" stroke="#45cfcd" stroke-width="1.8"><ellipse cx="20" cy="10" rx="10" ry="4"/><path d="M10 10v16c0 2 4 4 10 4s10-2 10-4V10M10 18c0 2 4 4 10 4s10-2 10-4"/><path d="M6 30h26v6H6zM32 30h6v6h-6"/><circle cx="12" cy="38" r="2.5"/><circle cx="32" cy="38" r="2.5"/></svg></div></div>
<div class="abs step-num" style="left:762px">03</div>
<h4 class="abs step-title" style="left:600px">Parcel In-Transit</h4>
<p class="abs step-text" style="left:600px">Quis ipsum suspendisse ultrices gravida. Risus commodo viverra maecenas accumsan facilisis.</p>

<div class="abs step-circle" style="left:919px"><div class="inner"><svg width="44" height="44" viewBox="0 0 44 44" fill="none" stroke="#45cfcd" stroke-width="1.8"><rect x="14" y="14" width="20" height="16"/><path d="M14 14l4-6h12l4 6M24 14v16"/><path d="M4 32h10l6 4h8"/><circle cx="34" cy="8" r="5"/><path d="m32 8 2 2 3-3M38 28v8M35 33l3 3 3-3"/></svg></div></div>
<div class="abs step-num" style="left:1016px">04</div>
<h4 class="abs step-title" style="left:854px">Parcel Delivery</h4>
<p class="abs step-text" style="left:854px">Quis ipsum suspendisse ultrices gravida. Risus commodo viverra maecenas accumsan facilisis.</p>

<!-- about -->
<div class="abs about-back"></div>
<div class="abs about-photo-a" role="img" aria-label="Front view of a white and red truck cab parked on a forecourt"></div>
<div class="abs about-stat"><b>25+</b><span>Years Working<br>Experience</span></div>
<div class="abs about-bar"></div>
<div class="abs about-photo-b" role="img" aria-label="White box truck on a road under a blue sky with clouds"></div>
<h2 class="abs about-title">About Us</h2>
<p class="abs about-text">Sed ut perspiciatis unde omnis iste natus error sit voluptatem accusantium doloremque laudantium, totam rem aperiam, eaque ipsa quae ab illo inventore veritatis et quasi architecto beatae vitae dicta sunt explicabo. Nemo enim ipsam vo-luptatem quia voluptas sit aspernatur aut odit aut fugit, sed quia consequuntur magni dolores eos qui ratione voluptatem sequi nesciunt. Neque porro quisquam est, qui dolorem ipsum quia dolor sit amet, consectetur, adipisci velit, sed quia non magnam aliquam quaerat voluptatem.</p>
<a class="abs btn about-btn">Read More</a>

<!-- blog -->
<h2 class="abs section-title" style="top:2493px">Our Blog</h2>

<article class="abs blog-card" style="left:111px">
  <div class="blog-photo" role="img" aria-label="Two trucks parked side by side at dusk" style="background:linear-gradient(180deg,#2b2d33 0%,#6c6660 45%,#b8a48a 70%,#3a3a3c 100%)"></div>
  <div class="blog-panel">
    <div class="blog-meta"><span class="blog-date">04 June</span><span>Comments (2)</span></div>
    <h3 class="blog-title">Sed ut perspiciatis unde omnis iste</h3>
    <p class="blog-text">Lorem ipsum dolor sit amet, con sectetur adipiscing elit, sed do labore et dolore magna aliqua.</p>
    <a class="read-more blog-more">Read More ...</a>
  </div>
</article>

<article class="abs blog-card" style="left:443px">
  <div class="blog-photo" role="img" aria-label="Row of parked truck cabs in bright colours" style="background:linear-gradient(90deg,#d9dde2 0%,#e58a3a 35%,#7d6a5c 60%,#b44a48 100%)"></div>
  <div class="blog-panel">
    <div class="blog-meta"><span class="blog-date">04 June</span><span>Comments (2)</span></div>
    <h3 class="blog-title">Sed ut perspiciatis unde omnis iste</h3>
    <p class="blog-text">Lorem ipsum dolor sit amet, con sectetur adipiscing elit, sed do labore et dolore magna aliqua.</p>
    <a class="read-more blog-more">Read More ...</a>
  </div>
</article>

<article class="abs blog-card" style="left:774px">
  <div class="blog-photo" role="img" aria-label="Aerial view of a rail freight yard full of container wagons" style="background:linear-gradient(100deg,#5d5a58 0%,#8a6a5a 30%,#4a6a78 55%,#9a8070 80%,#5a5c5a 100%)"></div>
  <div class="blog-panel">
    <div class="blog-meta"><span class="blog-date">04 June</span><span>Comments (2)</span></div>
    <h3 class="blog-title">Sed ut perspiciatis unde omnis iste</h3>
    <p class="blog-text">Lorem ipsum dolor sit amet, con sectetur adipiscing elit, sed do labore et dolore magna aliqua.</p>
    <a class="read-more blog-more">Read More ...</a>
  </div>
</article>

<div class="abs dots"><i class="on"></i><i></i><i></i></div>

<!-- footer -->
<footer class="abs footer"></footer>
<div class="abs foot-brand" style="color:#fff">Garvel Pryce Transport</div>
<div class="abs foot-divider"></div>
<div class="abs news-title" style="color:#fff">News Subscription</div>
<div class="abs news-sub" style="color:#fff">Get Latest Deals from Pryce's Inbox &amp; Subscribe Now</div>
<div class="abs news-input" style="color:#fff">Email Address
  <svg style="position:absolute;right:18px;top:17px" width="14" height="11" viewBox="0 0 14 11"><rect x=".8" y=".8" width="12.4" height="9.4" fill="none" stroke="#45cfcd" stroke-width="1.4"/><path d="m1 1 6 5 6-5" fill="none" stroke="#45cfcd" stroke-width="1.4"/></svg>
</div>
<a class="abs btn news-btn">Subscribe</a>
<div class="abs foot-rule"></div>

<div class="abs col-head" style="left:111px;color:#fff">About Company</div>
<div class="abs col-line" style="left:111px"></div>
<p class="abs foot-about" style="color:#fff">Lorem ipsum dolor sit amet, consectetur adipiscing elit, sed do eiusmod tempor incididunt ut labore et dolore magna aliqua.</p>
<div class="abs social" style="left:111px"></div>
<div class="abs social" style="left:169px"></div>
<div class="abs social" style="left:228px"></div>

<div class="abs col-head" style="left:396px;color:#fff">Quick Links</div>
<div class="abs col-line" style="left:396px"></div>
<ul class="abs link-list" style="left:396px;color:#fff">
  <li><span>›</span>Home</li><li><span>›</span>About Us</li><li><span>›</span>Services</li><li><span>›</span>Blog</li><li><span>›</span>Contact Us</li>
</ul>

<div class="abs col-head" style="left:612px;color:#fff">Other Links</div>
<div class="abs col-line" style="left:612px"></div>
<ul class="abs link-list" style="left:612px;color:#fff">
  <li><span>›</span>Help</li><li><span>›</span>Sitemap</li><li><span>›</span>Terms and conditions</li><li><span>›</span>Privacy policy</li><li><span>›</span>Cookies policy</li>
</ul>

<div class="abs col-head" style="left:858px;color:#fff">Recent Posts</div>
<div class="abs col-line" style="left:858px"></div>
<div class="abs recent" style="top:3410px;color:#fff">
  <div class="recent-photo" role="img" aria-label="Red truck on a city road" style="background:linear-gradient(180deg,#6a8fb8,#c23a34 60%,#555)"></div>
  <div><b>Lorem ipsum dolor sit amet, consectetur</b><small>▦ June 01 2023</small></div>
</div>
<div class="abs recent" style="top:3500px;color:#fff">
  <div class="recent-photo" role="img" aria-label="Truck travelling along a highway" style="background:linear-gradient(180deg,#9ab2cc,#e0e4e8 45%,#4b6a4b)"></div>
  <div><b>Lorem ipsum dolor sit amet, consectetur</b><small>▦ June 01 2023</small></div>
</div>

<div class="abs bottom-bar">Copyright © 2024 Garvel Pryce Transport. All rights reserved.</div>

</body>
</html>
```